ULMIRA card Technical Architecture

Hello everyone ULMIRA: It is a consulting firm in Architecture and Construction. I require a card duplexing, sober, elegant, classic but not boring. Update 1: Use the following data for the card. Name: Gonzalo Pereda Mauricio Villalta Position: COO Twitter: @ulmiraAT Homepage: ulmira-example.com home address not include the participation of all thank you.

Target Market(s)

Construction companies, Architects and Consulting Engineers

Industry/Entity Type

Consulting

Contact Information for Business Card

Los campos que debe tener:
Nombre, Cargo, email, homepage y twitter

Font styles to use
Serif
Sans Serif
Other font styles liked:
• Me gustan playfair display, open sans y roboto, pero estoy sujeto a sus propuestas

Requirements
Must have
• Colors: Present combined proposals in white, red, gray and black Update 1: The two names must be clearly differentiated from the two surnames
Nice to have
• They are free to present their best proposals. I will bring them immediate feedback to the extent you can go see their designs. Complete data for card and logo files will give the winner the

```html
<!DOCTYPE html>
<html lang="es">
<head>
<meta charset="utf-8">
<title>ULMIRA – Business Card</title>
<link rel="stylesheet" href="https://fonts.googleapis.com/css2?family=Open+Sans:wght@400;600;700&display=swap">
<style>
  :root {
    --backdrop: #3b3633;
    --card-black: #0c0c0c;
    --card-edge: #1a1a1a;
    --brand-red: #c8202c;
    --name-red: #e8344a;
    --text-white: #f2f2f2;
  }
  * { box-sizing: border-box; margin: 0; padding: 0; }
  html, body {
    width: 1200px; height: 900px; overflow: hidden;
    background: var(--backdrop);
    font-family: "Open Sans", Arial, sans-serif;
  }
  .card-set {
    position: absolute; top: 295px; left: 50px;
    display: flex; gap: 20px;
  }
  .card {
    position: relative; width: 540px; height: 310px;
    background: var(--card-black);
    border: 1px solid var(--card-edge);
    box-shadow: 0 14px 30px rgba(0,0,0,.45);
  }
  /* Contact side */
  .card--contact .brand-mark {
    position: absolute; left: 0; top: 0; width: 218px; height: 100%;
    display: flex; align-items: center; justify-content: center;
  }
  .brand-mark__name {
    color: var(--brand-red); font-weight: 700; font-size: 32px;
  }
  .divider {
    position: absolute; left: 218px; top: 60px; width: 1px; height: 190px;
    background: linear-gradient(to bottom, transparent, var(--brand-red) 45%, transparent);
  }
  .contact {
    position: absolute; left: 246px; top: 66px; color: var(--text-white);
  }
  .contact__name {
    color: var(--name-red); font-weight: 700; font-size: 17px; line-height: 21px;
  }
  .contact__name .surnames { display: block; }
  .contact__role { font-size: 13px; margin-top: 3px; }
  .contact__list { list-style: none; margin-top: 24px; font-size: 13px; }
  .contact__list li { display: flex; align-items: center; gap: 10px; height: 24px; }
  .contact__list li.social { margin-top: 8px; }
  .contact__icon { width: 12px; height: 12px; flex: none; }
  .social-square { width: 11px; height: 11px; background: var(--brand-red); border-radius: 2px; flex: none; }
  /* Name side */
  .card--logo .brand-name {
    position: absolute; inset: 0;
    display: flex; align-items: center; justify-content: center; gap: 12px;
    padding-bottom: 40px;
  }
  .brand-name__square { width: 14px; height: 14px; background: var(--brand-red); }
  .brand-name__text {
    color: var(--text-white); font-weight: 600; font-size: 36px; line-height: 1;
  }
</style>
</head>
<body>
  <main class="card-set">
    <section class="card card--contact">
      <div class="brand-mark"><span class="brand-mark__name">ULMIRA</span></div>
      <div class="divider"></div>
      <div class="contact">
        <p class="contact__name">Mauricio Gonzalo<span class="surnames">Pereda Villalta</span></p>
        <p class="contact__role">Director of Operations</p>
        <ul class="contact__list">
          <li>
            <svg class="contact__icon" viewBox="0 0 12 12" aria-hidden="true"><rect x="3" y="0.5" width="6" height="11" rx="1.2" fill="none" stroke="#c8202c" stroke-width="1.2"/><rect x="5" y="9" width="2" height="1" fill="#c8202c"/></svg>
            (+000) 555 555 0100
          </li>
          <li>
            <svg class="contact__icon" viewBox="0 0 12 12" aria-hidden="true"><circle cx="6" cy="6" r="5" fill="none" stroke="#c8202c" stroke-width="1.2"/><ellipse cx="6" cy="6" rx="2.2" ry="5" fill="none" stroke="#c8202c" stroke-width="1"/><line x1="1" y1="6" x2="11" y2="6" stroke="#c8202c" stroke-width="1"/></svg>
            www.ulmira-example.com
          </li>
          <li class="social"><span class="social-square"></span>@ulmiraAT</li>
        </ul>
      </div>
    </section>
    <section class="card card--logo">
      <div class="brand-name">
        <span class="brand-name__square"></span>
        <span class="brand-name__text">ULMIRA</span>
      </div>
    </section>
  </main>
</body>
</html>
```